Speisekarten-Design für gehobenes italienisches Restaurant
Zielgruppe
Wir sind ein gehobenes italienisches Restaurant und suchen ein neues Design für unsere Speisekarte. Wir haben ein eher älteres Publikum.
Aufgabenstellung
Wir möchten eine elegantes modernes Design. Einzelseiten im A4 Format.

```html
<!DOCTYPE html>
<html lang="de">
<head>
<meta charset="utf-8">
<title>Getränkekarte – Spritziges &amp; Klassiker</title>
<link href="https://fonts.googleapis.com/css2?family=Poiret+One&family=Marcellus&family=Lato:wght@400&display=swap" rel="stylesheet">
<style>
  :root {
    --backdrop: #e4e0da;
    --paper: #fbfbfa;
    --ink: #2b2a27;
    --ink-soft: #4a4843;
    --gold: #b8962e;
    --band: #f3dc96;
    --motif-a: #efeeec;
    --motif-b: #f9f9f8;
  }
  * { margin: 0; padding: 0; box-sizing: border-box; }
  html, body { width: 1200px; height: 900px; overflow: hidden; background: var(--backdrop); }
  .menu-page {
    position: absolute; left: 290px; top: 12px; width: 620px; height: 877px;
    background: var(--paper); box-shadow: 0 4px 18px rgba(0,0,0,.08);
    padding: 180px 64px 0 64px; color: var(--ink);
  }
  .menu-section { position: relative; z-index: 1; }
  .section-title {
    position: relative; display: inline-block;
    font-family: "Poiret One", sans-serif; font-size: 40px; letter-spacing: -1px; font-weight: 400;
    transform: scaleY(1.25); transform-origin: bottom left;
    padding: 0 6px 0 4px; margin-bottom: 14px; z-index: 0;
  }
  .section-title::after {
    content: ""; position: absolute; left: 0; right: -34px; bottom: -3px; height: 12px;
    background: var(--band); z-index: -1;
  }
  .drink { display: flex; align-items: flex-end; margin-bottom: 6px; }
  .drink-text { flex: 1; }
  .drink-name { font-family: "Marcellus", serif; color: var(--gold); font-size: 19px; line-height: 1.15; }
  .drink-desc { font-family: "Lato", sans-serif; font-size: 9.5px; color: var(--ink-soft); }
  .drink-volume, .drink-price { font-family: "Lato", sans-serif; font-size: 9.5px; color: var(--ink-soft); }
  .drink-volume { width: 40px; text-align: right; }
  .drink-price { width: 46px; text-align: right; }
  .section-classics { margin-top: 150px; }
  .motif {
    position: absolute; right: 40px; top: 440px; width: 290px; height: 330px; z-index: 0;
    background: radial-gradient(ellipse at 50% 45%, var(--motif-a), var(--motif-b) 70%, transparent 72%);
  }
</style>
</head>
<body>
<main class="menu-page">
  <div class="motif" role="img" aria-label="Dezente graue Linienillustration eines Löwenkopfes"></div>

  <section class="menu-section section-sparkling">
    <h2 class="section-title">SPRITZIGES</h2>
    <div class="drink"><div class="drink-text"><div class="drink-name">Hugo</div><div class="drink-desc">Prosecco Spumante, Holunderblütensirup, Soda, Pfefferminz</div></div><span class="drink-volume">0,2l</span><span class="drink-price">7,90</span></div>
    <div class="drink"><div class="drink-text"><div class="drink-name">Black Hugo</div><div class="drink-desc">Prosecco Spumante, Holunderblütensirup, Johannisbeersaft, Limette, Pfefferminz</div></div><span class="drink-volume">0,2l</span><span class="drink-price">7,90</span></div>
    <div class="drink"><div class="drink-text"><div class="drink-name">Aranzo Spritz</div><div class="drink-desc">Prosecco Spumante, Aranzo, Soda, Orangenscheibe</div></div><span class="drink-volume">0,2l</span><span class="drink-price">7,90</span></div>
    <div class="drink"><div class="drink-text"><div class="drink-name">Limoncello Spritz</div><div class="drink-desc">Prosecco Spumante, Limoncello, Soda, Zitrone</div></div><span class="drink-volume">0,2l</span><span class="drink-price">7,90</span></div>
    <div class="drink"><div class="drink-text"><div class="drink-name">Blanvin Wild Berry</div><div class="drink-desc">Blanvin, Prosecco Spumante, Weiße Beere Tonic, Beeren, Pfefferminz</div></div><span class="drink-volume">0,2l</span><span class="drink-price">8,90</span></div>
    <div class="drink"><div class="drink-text"><div class="drink-name">Lavendel Spritz</div><div class="drink-desc">Lavendelsirup, Prosecco Spumante, Soda, Zitrone</div></div><span class="drink-volume">0,2l</span><span class="drink-price">8,50</span></div>
    <div class="drink"><div class="drink-text"><div class="drink-name">Moscow Mule</div><div class="drink-desc">Nordstern Vodka, Limettensaft, Ginger Beer, Ingwer, Pfefferminz</div></div><span class="drink-volume">0,2l</span><span class="drink-price">10,90</span></div>
  </section>

  <section class="menu-section section-classics">
    <h2 class="section-title">KLASSIKER</h2>
    <div class="drink"><div class="drink-text"><div class="drink-name">Espresso Martini</div><div class="drink-desc">Espresso Shot, Nordstern Vodka, Cafetto Kaffee Likör, Crèmelia</div></div><span class="drink-volume"></span><span class="drink-price">10,90</span></div>
    <div class="drink"><div class="drink-text"><div class="drink-name">Negroni</div><div class="drink-desc">Rossamaro, Gin, Vallino Vermouth di Torino, Orangenscheibe</div></div><span class="drink-volume"></span><span class="drink-price">9,90</span></div>
    <div class="drink"><div class="drink-text"><div class="drink-name">Grand Ginger</div><div class="drink-desc">Gran Orangier, Ginger Ale, Limettensaft, Orangenscheibe</div></div><span class="drink-volume">0,2l</span><span class="drink-price">9,90</span></div>
  </section>
</main>
</body>
</html>
```